you will use Ai to Copy the website Brivanta.com to come up with the basic frame work and it will give you the understanding of how I would like Kelbrava.com to be like. Kelbrava.com is a peer to peer rv rental site very similar to both of the other rv rental sites the difference is that are commission based 20% and above per rental and we will be one flat monthly rate and they keep all the earnings. Below is photo that will help you with the color scheme and the look and feel of the design

1 page

```html
<!DOCTYPE html>
<html lang="en">
<head>
<meta charset="utf-8">
<title>Kelbrava.com – The Better Way to Rent an RV</title>
<link href="https://fonts.googleapis.com/css2?family=Outfit:wght@400;500;600;700&display=swap" rel="stylesheet">
<style>
:root{
  --navy:#0d1b33;
  --green:#5f9a2f;
  --green-dark:#4d8324;
  --ink:#1d2430;
  --muted:#5c6470;
  --line:#e2e5df;
  --band:#f3f5ee;
  --soft:#eef3e4;
  --star:#e8a93a;
  --white:#ffffff;
}
*{box-sizing:border-box;margin:0;padding:0}
html,body{width:1200px;height:2864px;overflow:hidden}
body{font-family:"Outfit",sans-serif;color:var(--ink);background:var(--white);position:relative}
.abs{position:absolute}
a{color:inherit;text-decoration:none}

/* nav */
.site-nav{left:0;top:0;width:1200px;height:64px;background:var(--navy)}
.brand{font-weight:700;font-size:29px;color:var(--white);letter-spacing:-.3px}
.nav-brand{left:36px;top:14px}
.nav-link{top:22px;font-size:14.5px;color:var(--white);font-weight:500}
.btn{display:flex;align-items:center;justify-content:center;font-weight:600;border-radius:5px}
.btn-solid{background:var(--green);color:var(--white)}
.btn-outline{border:2px solid var(--green);color:var(--green);background:var(--white);font-size:15px}
.nav-signup{left:1085px;top:13px;width:79px;height:38px;font-size:14.5px}

/* hero */
.hero{left:0;top:64px;width:1200px;height:553px}
.hero-photo{position:absolute;inset:0;background:
  linear-gradient(90deg,rgba(10,22,20,.75) 0%,rgba(10,22,20,.35) 45%,rgba(10,22,20,0) 70%),
  linear-gradient(180deg,#8c98a0 0%,#5d6e6c 25%,#34493a 55%,#2b3a28 80%,#4a4a3a 100%)}
.hero-title{left:64px;top:112px;font-size:63px;line-height:70px;font-weight:700;color:var(--white)}
.hero-sub{left:64px;top:266px;font-size:19px;line-height:31px;color:var(--white);font-weight:500}
.search{left:64px;top:352px;width:702px;height:59px;background:var(--white);border-radius:6px;display:flex;align-items:center;font-size:12.5px;color:var(--muted)}
.search-field{display:flex;align-items:center;gap:9px;height:100%;padding-left:22px;border-right:1px solid var(--line)}
.search-btn{position:absolute;right:0;top:0;width:108px;height:59px;font-size:16px;border-radius:6px}
.perk{top:448px;display:flex;gap:8px;color:var(--white)}
.perk b{display:block;font-size:14px;font-weight:600}
.perk span{display:block;font-size:12px;opacity:.8;margin-top:4px}

/* trust */
.trust{left:0;top:617px;width:1200px;height:117px;background:var(--band)}
.trust-text{top:51px;font-size:15px;color:var(--ink)}
.stars{left:340px;top:48px;display:flex;gap:3px}
.avatar{width:32px;height:32px;border-radius:50%;border:2px solid var(--white);top:45px}

/* sections */
.section-title{left:0;width:1200px;text-align:center;font-size:29px;font-weight:600;color:var(--ink)}
.section-sub{left:0;width:1200px;text-align:center;font-size:14.5px;color:var(--muted)}
.card{border:1px solid var(--line);border-radius:6px;background:var(--white);overflow:hidden;text-align:center}
.card-photo{width:100%}
.card-name{font-size:15px;font-weight:600;margin-top:18px}
.card-count{font-size:12.5px;color:var(--muted);margin-top:12px}

/* steps */
.step-icon{width:104px;height:104px;border-radius:50%;background:var(--soft);display:flex;align-items:center;justify-content:center}
.step-dash{top:1446px;width:60px;border-top:2px dashed #c6cbc2}
.step-text{width:200px;text-align:center}
.step-text b{display:block;font-size:15px;font-weight:600}
.step-text span{display:block;font-size:13px;color:var(--muted);line-height:21px;margin-top:10px}

/* owner band */
.owner-band{left:63px;top:1699px;width:1076px;height:268px;border-radius:8px;overflow:hidden}
.owner-photo{position:absolute;inset:0;background:
  linear-gradient(90deg,rgba(16,26,22,.92) 0%,rgba(16,26,22,.7) 45%,rgba(16,26,22,.15) 80%),
  linear-gradient(180deg,#6d7a7a 0%,#3e5142 50%,#2d3b2a 100%)}
.owner-title{left:53px;top:32px;font-size:31px;line-height:41px;font-weight:600;color:var(--white)}
.owner-body{left:53px;top:124px;font-size:16.5px;line-height:28px;color:var(--white)}
.owner-btn{left:53px;top:194px;width:152px;height:40px;font-size:15px}
.owner-point{left:481px;display:flex;align-items:center;gap:12px;font-size:13.5px;font-weight:500;color:var(--white)}
.tick{width:27px;height:27px;border-radius:50%;background:var(--green);display:flex;align-items:center;justify-content:center}

/* cta */
.cta{left:34px;top:2422px;width:1129px;height:102px;background:var(--band);border-radius:8px}
.cta-art{left:74px;top:19px;width:160px;height:64px;background:linear-gradient(180deg,#f3f5ee,#dfe6d2);border-radius:4px}
.cta-title{left:270px;top:26px;font-size:23px;font-weight:600}
.cta-sub{left:270px;top:62px;font-size:14.5px;color:var(--muted)}
.cta-btn{left:820px;top:31px;width:173px;height:42px;font-size:15px}

/* footer */
.footer{left:0;top:2582px;width:1200px;height:282px;background:var(--navy);color:var(--white)}
.foot-about{left:39px;top:98px;width:230px;font-size:12.5px;line-height:22px;opacity:.9}
.foot-social{top:175px;width:22px;height:22px;border-radius:50%;border:2px solid var(--white)}
.foot-col{top:56px}
.foot-col h4{font-size:16px;font-weight:600;margin-bottom:14px}
.foot-col li{list-style:none;font-size:12.5px;line-height:28px;opacity:.9}
.foot-form{left:898px;top:120px;display:flex}
.foot-input{width:162px;height:37px;background:var(--white);color:#8a8f96;font-size:12.5px;padding:11px 12px;border-radius:3px 0 0 3px}
.foot-sub{width:87px;height:37px;font-size:13px;border-radius:0 3px 3px 0}
.copyright{left:0;top:233px;width:1200px;text-align:center;font-size:14px;opacity:.9}
</style>
</head>
<body>

<header class="abs site-nav">
  <a class="abs brand nav-brand" href="#">Kelbrava.com</a>
  <a class="abs nav-link" style="left:572px" href="#">How It Works</a>
  <a class="abs nav-link" style="left:686px" href="#">Browse RVs</a>
  <a class="abs nav-link" style="left:791px" href="#">List Your RV</a>
  <a class="abs nav-link" style="left:897px" href="#">Resources
    <svg width="10" height="7" viewBox="0 0 10 7" style="margin-left:6px"><path d="M1 1l4 4 4-4" stroke="#fff" stroke-width="1.6" fill="none"/></svg></a>
  <a class="abs nav-link" style="left:1016px" href="#">Log In</a>
  <a class="abs btn btn-solid nav-signup" href="#">Sign Up</a>
</header>

<section class="abs hero">
  <div class="hero-photo" role="img" aria-label="Motorhome parked on a mountain road beside a lake with pine forest and snowy peaks"></div>
  <h1 class="abs hero-title">The Better Way<br>to Rent an RV</h1>
  <p class="abs hero-sub">Rent directly from RV owners and save.<br>No hidden fees, just memorable adventures.</p>
  <form class="abs search">
    <div class="search-field" style="width:238px">
      <svg width="14" height="16" viewBox="0 0 14 16"><path d="M7 15s5-5 5-9A5 5 0 0 0 2 6c0 4 5 9 5 9z" stroke="#555" stroke-width="1.4" fill="none"/><circle cx="7" cy="6" r="1.8" stroke="#555" stroke-width="1.4" fill="none"/></svg>Enter destination</div>
    <div class="search-field" style="width:222px">
      <svg width="14" height="14" viewBox="0 0 14 14"><rect x="1" y="2" width="12" height="11" rx="1.5" stroke="#555" stroke-width="1.4" fill="none"/><path d="M1 5.5h12M4 0.5v3M10 0.5v3" stroke="#555" stroke-width="1.4"/></svg>Pick up <span style="margin:0 14px">–</span> Drop off</div>
    <div class="search-field" style="border:none">
      <svg width="14" height="14" viewBox="0 0 14 14"><circle cx="7" cy="4.5" r="3" stroke="#555" stroke-width="1.4" fill="none"/><path d="M1.5 13.5c0-3 2.5-5 5.5-5s5.5 2 5.5 5" stroke="#555" stroke-width="1.4" fill="none"/></svg>Guests</div>
    <div class="btn btn-solid search-btn">Search</div>
  </form>
  <div class="abs perk" style="left:65px">
    <svg width="18" height="18" viewBox="0 0 18 18"><path d="M2 13V8a7 7 0 0 1 14 0v5M2 11h3v4H2zM13 11h3v4h-3z" stroke="#fff" stroke-width="1.5" fill="none"/></svg>
    <div><b>Wide selection</b><span>Find the perfect RV</span></div></div>
  <div class="abs perk" style="left:240px">
    <svg width="18" height="18" viewBox="0 0 18 18"><rect x="2" y="4" width="14" height="12" rx="2" stroke="#fff" stroke-width="1.5" fill="none"/><path d="M6 4V2h6v2M6 10l2 2 4-4" stroke="#fff" stroke-width="1.5" fill="none"/></svg>
    <div><b>Best prices</b><span>No middleman fees</span></div></div>
  <div class="abs perk" style="left:413px">
    <svg width="18" height="18" viewBox="0 0 18 18"><circle cx="9" cy="9" r="7" stroke="#fff" stroke-width="1.5" fill="none"/><path d="M9 5v4l3 2" stroke="#fff" stroke-width="1.5" fill="none"/></svg>
    <div><b>24/7 support</b><span>We're here to help</span></div></div>
</section>

<section class="abs trust">
  <p class="abs trust-text" style="left:66px">Trusted by thousands of travelers</p>
  <div class="abs stars" role="img" aria-label="Five star rating">
    <svg width="21" height="21" viewBox="0 0 24 24"><path d="M12 2l3 7h7l-5.5 4.5 2 7.5-6.5-4.5L5.5 21l2-7.5L2 9h7z" fill="var(--star)"/></svg>
    <svg width="21" height="21" viewBox="0 0 24 24"><path d="M12 2l3 7h7l-5.5 4.5 2 7.5-6.5-4.5L5.5 21l2-7.5L2 9h7z" fill="var(--star)"/></svg>
    <svg width="21" height="21" viewBox="0 0 24 24"><path d="M12 2l3 7h7l-5.5 4.5 2 7.5-6.5-4.5L5.5 21l2-7.5L2 9h7z" fill="var(--star)"/></svg>
    <svg width="21" height="21" viewBox="0 0 24 24"><path d="M12 2l3 7h7l-5.5 4.5 2 7.5-6.5-4.5L5.5 21l2-7.5L2 9h7z" fill="var(--star)"/></svg>
    <svg width="21" height="21" viewBox="0 0 24 24"><path d="M12 2l3 7h7l-5.5 4.5 2 7.5-6.5-4.5L5.5 21l2-7.5L2 9h7z" fill="var(--star)"/></svg>
  </div>
  <p class="abs trust-text" style="left:479px;font-size:14.5px">4.8 rating on <span style="font-weight:600">Revuely</span></p>
  <div class="abs avatar" role="img" aria-label="Traveler portrait" style="left:754px;background:#8a6a55"></div>
  <div class="abs avatar" role="img" aria-label="Traveler portrait" style="left:781px;background:#6f7578"></div>
  <div class="abs avatar" role="img" aria-label="Traveler portrait" style="left:809px;background:#b59a84"></div>
  <div class="abs avatar" role="img" aria-label="Traveler portrait" style="left:837px;background:#7a5a44"></div>
  <div class="abs avatar" role="img" aria-label="Traveler portrait" style="left:865px;background:#a08570"></div>
  <p class="abs trust-text" style="left:912px;font-size:14.5px">10,000+ happy adventurers</p>
</section>

<h2 class="abs section-title" style="top:776px">Browse RVs for Every Adventure</h2>
<p class="abs section-sub" style="top:826px">From cozy campervans to luxury motorhomes, find the perfect RV for your next trip.</p>

<div class="abs card" style="left:50px;top:877px;width:201px;height:306px">
  <div class="card-photo" role="img" aria-label="Campervan parked by a palm-lined ocean shore" style="height:224px;background:linear-gradient(180deg,#b9d3e4,#7fa9c0 45%,#9a9690)"></div>
  <p class="card-name">Campervans</p><p class="card-count">1,000+ RVs</p></div>
<div class="abs card" style="left:269px;top:877px;width:206px;height:306px">
  <div class="card-photo" role="img" aria-label="Travel trailer in an alpine meadow below mountains" style="height:224px;background:linear-gradient(180deg,#a9c4da,#6d8a7a 45%,#5c7a3c)"></div>
  <p class="card-name">Travel Trailers</p><p class="card-count">2,000+ RVs</p></div>
<div class="abs card" style="left:494px;top:877px;width:206px;height:306px">
  <div class="card-photo" role="img" aria-label="Class C motorhome on a forest road with autumn trees" style="height:224px;background:linear-gradient(180deg,#a8bfcf,#7b8a5e 40%,#8a7a4a)"></div>
  <p class="card-name">Class C</p><p class="card-count">1,500+ RVs</p></div>
<div class="abs card" style="left:719px;top:877px;width:206px;height:306px">
  <div class="card-photo" role="img" aria-label="Class A motorhome in a green mountain valley" style="height:224px;background:linear-gradient(180deg,#8f8f86,#5d6c48 45%,#5b6a3e)"></div>
  <p class="card-name">Class A</p><p class="card-count">800+ RVs</p></div>
<div class="abs card" style="left:943px;top:877px;width:205px;height:306px">
  <div class="card-photo" role="img" aria-label="Toy hauler trailer with open ramp and bicycles" style="height:224px;background:linear-gradient(180deg,#c8d8e6,#7c7668 45%,#6f8a50)"></div>
  <p class="card-name">Toy Haulers</p><p class="card-count">500+ RVs</p></div>

<a class="abs btn btn-outline" style="left:514px;top:1211px;width:159px;height:40px" href="#">Browse All RVs</a>

<h2 class="abs section-title" style="top:1293px">How Kelbrava.com Works</h2>
<p class="abs section-sub" style="top:1344px">Renting an RV has never been easier</p>

<div class="abs step-icon" style="left:213px;top:1394px"><svg width="50" height="50" viewBox="0 0 50 50"><circle cx="21" cy="21" r="14" stroke="#1d2430" stroke-width="3" fill="none"/><path d="M31 31l12 12" stroke="#1d2430" stroke-width="3" stroke-linecap="round"/></svg></div>
<div class="abs step-dash" style="left:343px"></div>
<div class="abs step-icon" style="left:429px;top:1394px"><svg width="54" height="50" viewBox="0 0 54 50"><path d="M4 18c0-8 8-14 17-14s17 6 17 14-8 14-17 14c-2 0-4 0-6-1l-8 5 2-7c-3-3-5-7-5-11z" stroke="#1d2430" stroke-width="2.6" fill="none"/><path d="M30 30c2 4 7 7 12 7l7 4-1-7c3-2 4-5 4-8 0-4-2-7-6-9" stroke="#1d2430" stroke-width="2.6" fill="none"/><circle cx="36" cy="27" r="1.8" fill="#1d2430"/><circle cx="41" cy="27" r="1.8" fill="#1d2430"/><circle cx="46" cy="27" r="1.8" fill="#1d2430"/></svg></div>
<div class="abs step-dash" style="left:560px"></div>
<div class="abs step-icon" style="left:646px;top:1394px"><svg width="50" height="50" viewBox="0 0 50 50"><circle cx="17" cy="12" r="8" stroke="#1d2430" stroke-width="2.6" fill="none"/><path d="M17 20v24l-4-3M17 34h4M17 40h4" stroke="#1d2430" stroke-width="2.6" fill="none"/><circle cx="34" cy="14" r="8" stroke="#1d2430" stroke-width="2.6" fill="none"/><path d="M31 22l-5 22 5-2 2 4" stroke="#1d2430" stroke-width="2.6" fill="none"/></svg></div>
<div class="abs step-dash" style="left:778px"></div>
<div class="abs step-icon" style="left:864px;top:1394px"><svg width="50" height="50" viewBox="0 0 24 24"><path d="M12 2.5l2.9 6.2 6.8.7-5.1 4.6 1.5 6.7L12 17.3l-6.1 3.4 1.5-6.7-5.1-4.6 6.8-.7z" stroke="#1d2430" stroke-width="1.3" fill="none" stroke-linejoin="round"/></svg></div>

<div class="abs step-text" style="left:165px;top:1520px"><b>1. Search</b><span>Find the perfect RV<br>for your trip</span></div>
<div class="abs step-text" style="left:381px;top:1520px"><b>2. Book</b><span>Connect with owners<br>and book securely</span></div>
<div class="abs step-text" style="left:598px;top:1520px"><b>3. Hit the Road</b><span>Pick up your RV and<br>start your adventure</span></div>
<div class="abs step-text" style="left:816px;top:1520px"><b>4. Share &amp; Review</b><span>Share your experience<br>and help others</span></div>

<a class="abs btn btn-outline" style="left:526px;top:1621px;width:140px;height:40px" href="#">Learn More</a>

<section class="abs owner-band">
  <div class="owner-photo" role="img" aria-label="Class C motorhome parked in a misty mountain forest"></div>
  <h2 class="abs owner-title">List Your RV and<br>Start Earning</h2>
  <p class="abs owner-body">Join thousands of RV owners earning extra<br>income on their terms.</p>
  <a class="abs btn btn-solid owner-btn" href="#">List Your RV</a>
  <div class="abs owner-point" style="top:47px"><span class="tick"><svg width="13" height="13" viewBox="0 0 13 13"><path d="M2 7l3 3 6-7" stroke="#fff" stroke-width="2" fill="none"/></svg></span>Keep 100% of your earnings</div>
  <div class="abs owner-point" style="top:96px"><span class="tick"><svg width="13" height="13" viewBox="0 0 13 13"><path d="M2 7l3 3 6-7" stroke="#fff" stroke-width="2" fill="none"/></svg></span>One flat monthly rate</div>
  <div class="abs owner-point" style="top:144px"><span class="tick"><svg width="13" height="13" viewBox="0 0 13 13"><path d="M2 7l3 3 6-7" stroke="#fff" stroke-width="2" fill="none"/></svg></span>No hidden fees</div>
  <div class="abs owner-point" style="top:193px"><span class="tick"><svg width="13" height="13" viewBox="0 0 13 13"><path d="M2 7l3 3 6-7" stroke="#fff" stroke-width="2" fill="none"/></svg></span>24/7 owner support</div>
</section>

<h2 class="abs section-title" style="top:1997px">Explore Popular Destinations</h2>
<p class="abs section-sub" style="top:2043px">Find inspiration for your next adventure</p>

<div class="abs card" style="left:48px;top:2083px;width:207px;height:251px">
  <div class="card-photo" role="img" aria-label="Red rock canyon with a winding river" style="height:183px;background:linear-gradient(180deg,#b9cbd8,#b0674a 45%,#8a5a3e)"></div>
  <p class="card-name" style="font-size:13px;margin-top:14px">Zion National Park</p><p class="card-count" style="margin-top:9px">1,200+ RVs</p></div>
<div class="abs card" style="left:272px;top:2083px;width:207px;height:251px">
  <div class="card-photo" role="img" aria-label="Coastal bridge over a rocky ocean cove" style="height:183px;background:linear-gradient(180deg,#9fb6c4,#5f7a6a 45%,#3f7f86)"></div>
  <p class="card-name" style="font-size:13px;margin-top:14px">California Coast</p><p class="card-count" style="margin-top:9px">2,500+ RVs</p></div>
<div class="abs card" style="left:495px;top:2083px;width:207px;height:251px">
  <div class="card-photo" role="img" aria-label="Turquoise mountain lake reflecting forested peaks" style="height:183px;background:linear-gradient(180deg,#a6c2dc,#4f7a52 45%,#2f8f8a)"></div>
  <p class="card-name" style="font-size:13px;margin-top:14px">Rocky Mountains</p><p class="card-count" style="margin-top:9px">1,800+ RVs</p></div>
<div class="abs card" style="left:718px;top:2083px;width:207px;height:251px">
  <div class="card-photo" role="img" aria-label="Desert sunset with saguaro cacti" style="height:183px;background:linear-gradient(180deg,#c94a3a,#e0783a 45%,#5a2f2a)"></div>
  <p class="card-name" style="font-size:13px;margin-top:14px">Arizona Desert</p><p class="card-count" style="margin-top:9px">1,100+ RVs</p></div>
<div class="abs card" style="left:942px;top:2083px;width:207px;height:251px">
  <div class="card-photo" role="img" aria-label="Waterfalls in a lush green forest" style="height:183px;background:linear-gradient(180deg,#2f4a2a,#5d8a3c 50%,#2c3f24)"></div>
  <p class="card-name" style="font-size:13px;margin-top:14px">Pacific Northwest</p><p class="card-count" style="margin-top:9px">1,600+ RVs</p></div>

<a class="abs btn btn-outline" style="left:515px;top:2353px;width:157px;height:40px" href="#">Explore More</a>

<section class="abs cta">
  <div class="abs cta-art" role="img" aria-label="Line drawing of a camper van beside pine trees"></div>
  <h2 class="abs cta-title">Ready to start your adventure?</h2>
  <p class="abs cta-sub">Join Kelbrava.com today and find your perfect RV.</p>
  <a class="abs btn btn-solid cta-btn" href="#">Sign Up Now</a>
</section>

<footer class="abs footer">
  <p class="abs brand" style="left:39px;top:38px">Kelbrava.com</p>
  <p class="abs foot-about">The peer-to-peer RV rental marketplace where owners earn more and renters adventure more.</p>
  <span class="abs foot-social" style="left:39px"></span>
  <span class="abs foot-social" style="left:78px"></span>
  <span class="abs foot-social" style="left:120px"></span>
  <div class="abs foot-col" style="left:311px"><h4>Explore</h4><ul><li>Find an RV</li><li>List Your RV</li><li>How It Works</li><li>Destinations</li></ul></div>
  <div class="abs foot-col" style="left:509px"><h4>Support</h4><ul><li>Help Center</li><li>Safety</li><li>Terms of Service</li><li>Privacy Policy</li></ul></div>
  <div class="abs foot-col" style="left:709px"><h4>Company</h4><ul><li>About Us</li><li>Careers</li><li>Contact Us</li><li>Blog</li></ul></div>
  <div class="abs foot-col" style="left:898px"><h4>Stay Connected</h4><ul><li>Get tips, ideas, and RV deals.</li></ul></div>
  <div class="abs foot-form"><div class="foot-input">Enter your email</div><div class="btn btn-solid foot-sub">Subscribe</div></div>
  <p class="abs copyright">© 2026 kelbrava.com, All rights reserved.</p>
</footer>

</body>
</html>
```